Stationary Set Rebrand for Brennick

We are a Canadian Distribution and Service Company that was established in 1969. Over the past 5 decades we have expanded our business and have warehouses across Canada. We specialize in adhesive tapes, adhesives, films, safety, warehouse, shipping, janitorial and packaging supplies.

We have updated our logo design and would like a new corporate branding identity that includes a new fresh Stationary Set (Business Cards, Letterhead, Letterhead MS Word, Envelope, Presentation Folders, Email Signatures, Notepad Covers, etc.)

Target Market(s)

Industrial Business Sector

Font styles to use
Sans Serif

Colors
0054AA
0677BA
7BADD7
CADEEF
E8F1F8
0094D4
00A9DD
6FCCEA
C7EBF8
E9F6FB
00AB8E
00BBA5
67D7C9
C6EFE9
E9F9F6
EB3D1F
EC4F4E
F09395
F8D3D4
FCEDEE

Requirements
Should not have
• Colors not too light, darker colours preferred

```html
<!DOCTYPE html>
<html lang="en">
<head>
<meta charset="utf-8">
<title>Brennick Business Card</title>
<link rel="stylesheet" href="https://fonts.googleapis.com/css2?family=Montserrat:wght@400;600;800&display=swap">
<style>
  :root {
    --bg: #d3d8d8;
    --card: #f1f1ef;
    --ink: #111111;
    --accent: #d3121a;
    --muted: #2a2a2a;
  }
  * { margin: 0; padding: 0; box-sizing: border-box; }
  html, body { width: 1200px; height: 881px; overflow: hidden; }
  body {
    background: var(--bg);
    font-family: "Montserrat", Arial, sans-serif;
    color: var(--ink);
    position: relative;
  }
  .card {
    position: absolute;
    width: 520px;
    height: 298px;
    background: var(--card);
    border-bottom: 5px solid var(--accent);
    box-shadow: 0 18px 40px rgba(0,0,0,0.18);
  }
  .card--front { left: 50px; top: 330px; }
  .card--back { left: 630px; top: 250px; }

  .brand {
    position: absolute;
    display: flex;
    align-items: center;
    gap: 14px;
  }
  .brand__name {
    font-weight: 800;
    color: var(--ink);
    line-height: 1;
    letter-spacing: -1px;
  }
  .brand__mark {
    background: var(--accent);
    flex: none;
  }
  .tagline {
    position: absolute;
    font-weight: 600;
    color: var(--ink);
  }

  .card--front .brand { left: 40px; top: 30px; }
  .card--front .brand__name { font-size: 72px; }
  .card--front .brand__mark { width: 18px; height: 18px; margin-top: 30px; }
  .card--front .tagline { left: 42px; top: 110px; font-size: 17px; }

  .card--back .brand { left: 50%; top: 90px; transform: translateX(-50%); }
  .card--back .brand__name { font-size: 84px; }
  .card--back .brand__mark { width: 20px; height: 20px; margin-top: 36px; }
  .card--back .tagline { left: 0; right: 0; top: 188px; text-align: center; font-size: 19px; }

  .person {
    position: absolute;
    left: 40px;
    top: 160px;
    width: 200px;
    text-align: right;
  }
  .person__name { color: var(--accent); font-weight: 600; font-size: 21px; }
  .person__title { font-size: 12px; color: var(--muted); margin-top: 4px; }

  .divider {
    position: absolute;
    left: 256px;
    top: 160px;
    width: 2px;
    height: 62px;
    background: var(--accent);
  }
  .contact {
    position: absolute;
    left: 272px;
    top: 160px;
    list-style: none;
    font-size: 12.5px;
    color: var(--muted);
  }
  .contact li { display: flex; align-items: center; gap: 8px; height: 21px; }
  .contact svg { width: 12px; height: 12px; fill: var(--accent); flex: none; }

  .address {
    position: absolute;
    left: 0; right: 0;
    top: 250px;
    text-align: center;
    font-size: 13px;
    color: var(--muted);
  }
</style>
</head>
<body>

<section class="card card--front">
  <div class="brand">
    <span class="brand__name">Brennick</span>
    <span class="brand__mark"></span>
  </div>
  <p class="tagline">Tape and Packaging Specialists</p>

  <div class="person">
    <p class="person__name">Daniel Marsh</p>
    <p class="person__title">Managing Director</p>
  </div>
  <div class="divider"></div>
  <ul class="contact">
    <li>
      <svg viewBox="0 0 24 24" aria-hidden="true"><path d="M6.6 10.8a15 15 0 0 0 6.6 6.6l2.2-2.2c.3-.3.7-.4 1-.2 1.1.4 2.3.6 3.6.6.6 0 1 .4 1 1V20c0 .6-.4 1-1 1A17 17 0 0 1 3 4c0-.6.4-1 1-1h3.5c.6 0 1 .4 1 1 0 1.3.2 2.5.6 3.6.1.3 0 .7-.2 1z"/></svg>
      123 456 789
    </li>
    <li>
      <svg viewBox="0 0 24 24" aria-hidden="true"><path d="M2 5h20v14H2z M2 5l10 8 10-8" stroke="#f1f1ef" stroke-width="1.5"/></svg>
      info@brennickmail.com
    </li>
    <li>
      <svg viewBox="0 0 24 24" aria-hidden="true"><circle cx="12" cy="12" r="10"/></svg>
      www.brennickwebsite.com
    </li>
  </ul>
  <p class="address">Your address, City State, Zip 1234</p>
</section>

<section class="card card--back">
  <div class="brand">
    <span class="brand__name">Brennick</span>
    <span class="brand__mark"></span>
  </div>
  <p class="tagline">Tape and Packaging Specialists</p>
</section>

</body>
</html>
```